Wordpress Powered Website. Outstanding Design Required. Using Morvenic Theme

Designers will not need to create anything other than the home page but there are some design elements on the home page which also need to be factored in: 6 product place holders and 2-3 slides for a slideshow (with images I provide).

Designers will need to familiarise themselves with the Morvenic theme to make sure that their design will work within the theme.

The winning designer will set up all the pages and navigation in place. This includes social media icons, favicon, widgets, etc. In other words, the home page needs to be designed and coded and the other preset theme pages need to be organised in a way that we can start using the website on completion of the job.

Most of the designs I had last time were too colourful. This needs to be subtle not in your face.

Background to the business/website:
Ridgeway Banners is a new Australian venture which will sell large format printed banners and other signage. The market is very competitive so it is important to stand out visually and to have a website which is clean, easy to navigate and easy to order. It will be a combination of online sales and assisted sales but all sales enquiries will come from the website.

As our business is focused on presentation it is vital to have excellent design.
Purchased theme is Morvenic. Only this theme is to be used.

1. A home page using all the preset features of the Morvenic theme - it will just be basically taking my wireframe and inputting it to the live theme.
2. A three slide slideshow, ideally with an edited video. The static image slides can be provided by me during the handover. Placeholder for now.
Similar to this one: http://thecedarhollow.example.au/

Attached is the logo which must be utilised, although it could also sit on a dark background. There is our mascot as well which can be used but does not have to be included.

Target Market(s)

Primarily B2B (business to business)
Main industries will be Construction, Retail, Community, Events & Trade Shows

Industry/Entity Type

Printing

Coding

Coded - Design and coding required

Font styles to use
Sans Serif

Requirements
Must have
• Must have the design files made to web pages within the Wordpress environment.
Nice to have
• Clean design. Stand out from competitors based on design.
Should not have
• Should not look like any competitor

```html
<!DOCTYPE html>
<html lang="en">
<head>
<meta charset="utf-8">
<title>Ridgeway Banners</title>
<link href="https://fonts.googleapis.com/css2?family=Montserrat:wght@500;600;700&family=Open+Sans:ital,wght@0,400;0,600;0,700;1,400;1,600;1,700&family=Oswald:wght@400&display=swap" rel="stylesheet">
<style>
:root{
  --blue:#1b6fce;
  --blue-dark:#1559a8;
  --ink:#222;
  --text:#444;
  --muted:#777;
  --topbar:#151515;
  --light:#f2f2f2;
  --yellow:#ffe100;
  --green-a:#4f8f25;
  --green-b:#8dc63f;
  --footer:#1c1c1c;
  --white:#fff;
}
*{box-sizing:border-box;margin:0;padding:0}
html,body{width:1200px;height:2711px;overflow:hidden}
body{font-family:"Open Sans",Arial,sans-serif;color:var(--text);background:var(--white);position:relative}
.abs{position:absolute}
section,header,footer{position:absolute;left:0;width:1200px;overflow:hidden}

/* top bar */
.topbar{top:0;height:36px;background:var(--topbar);color:#fff;font-size:13px;font-weight:600}
.social{display:flex;gap:13px;position:absolute;left:99px;top:11px}
.social span{width:14px;height:14px;border-radius:50%;background:#fff;display:block}
.contact-item{position:absolute;top:9px;display:flex;align-items:center;gap:8px;white-space:nowrap;line-height:18px}

/* header */
.site-header{top:36px;height:83px;background:#fff;border-bottom:1px solid #e3e3e3}
.brand{position:absolute;left:99px;top:22px;display:flex;align-items:center;gap:12px;font-family:"Montserrat",sans-serif;font-weight:700;font-size:28px;color:var(--blue);letter-spacing:.3px;white-space:nowrap}
.brand i{width:28px;height:28px;background:var(--blue);border-radius:50%;display:block}
.nav{position:absolute;top:25px;left:506px;width:596px;display:flex;align-items:center;justify-content:space-between;font-family:"Open Sans",sans-serif;font-weight:600;font-size:13px;color:#333;white-space:nowrap}
.nav a{text-decoration:none;color:inherit;padding:7px 0}
.nav .sep{width:1px;height:14px;background:#ccc}
.nav .current{background:var(--blue);color:#fff;padding:8px 18px}

/* hero */
.hero{top:119px;height:429px;background:linear-gradient(180deg,#5d7388 0%,#44586b 45%,#243446 70%,#1b2a3a 100%)}
.hero-title{position:absolute;left:101px;top:145px;font-family:"Oswald",sans-serif;font-weight:400;font-size:25px;line-height:34px;color:#fff;width:420px}
.btn-yellow{position:absolute;left:101px;top:264px;width:150px;height:33px;background:var(--yellow);color:#222;font-weight:700;font-size:14px;display:flex;align-items:center;justify-content:center;border-radius:2px}
.tile{position:absolute;border:3px solid #fff;box-shadow:0 2px 6px rgba(0,0,0,.4)}
.dots{position:absolute;left:101px;top:397px;display:flex;gap:9px}
.dots span{width:13px;height:13px;border-radius:50%;border:2px solid #fff}
.dots .on{background:var(--blue)}

/* section titles */
.sec-title{position:absolute;left:0;width:1200px;text-align:center;font-family:"Montserrat",sans-serif;font-weight:700;color:var(--ink)}
.rule{position:absolute;height:1px;background:#ddd}
.btn-outline{position:absolute;border:1.5px solid var(--blue);color:var(--blue);font-family:"Montserrat",sans-serif;font-weight:600;font-size:12px;display:flex;align-items:center;justify-content:center;letter-spacing:.3px;background:#fff}

/* about */
.about{top:548px;height:256px;background:#fff}
.about p{position:absolute;left:105px;top:102px;width:990px;font-size:12px;line-height:23px;text-align:center;color:#555}

/* features */
.features{top:804px;height:407px;background:var(--light)}
.feature{position:absolute;top:51px;width:240px;text-align:center}
.feature .icon{width:112px;height:112px;border-radius:50%;background:var(--blue);margin:0 auto;display:flex;align-items:center;justify-content:center}
.feature h3{font-family:"Montserrat",sans-serif;font-weight:600;font-size:16px;color:var(--ink);margin-top:20px}
.feature p{font-size:12px;line-height:23.5px;color:#555;margin-top:24px;padding:0 10px}
.feature .btn-outline{position:relative;margin:20px auto 0;width:121px;height:31px}

/* products */
.products{top:1211px;height:564px;background:linear-gradient(135deg,#5a5e66,#3c4048 50%,#5b5347)}
.products .shade{position:absolute;inset:0;background:rgba(20,22,26,.45)}
.products .sec-title{color:#fff;top:50px;font-size:24px}
.card{position:absolute;width:240px;height:181px;text-align:center}
.card.white{background:#fff}
.card.blue{background:var(--blue);color:#fff}
.card h4{font-family:"Open Sans",sans-serif;font-weight:600;font-size:18px;margin-top:18px}
.card.white h4{color:#222}
.card p{font-size:12px;line-height:19px;margin:8px 18px 0}
.card.white p{color:#555}
.card .btn-outline{position:relative;margin:12px auto 0;width:121px;height:31px}
.card.blue .btn-outline{background:transparent;border-color:#fff;color:#fff}
.photo{position:absolute;width:240px;height:181px}

/* why */
.why{top:1775px;height:357px;background:var(--light)}
.why h2{position:absolute;left:101px;top:40px;font-family:"Montserrat",sans-serif;font-weight:700;font-size:23px;color:var(--ink)}
.why h2 b{color:var(--blue);font-weight:700}
.why p{position:absolute;left:101px;top:99px;width:460px;font-size:12px;line-height:23px;color:#444}
.perk{position:absolute;display:flex;align-items:center;gap:14px;font-family:"Montserrat",sans-serif;font-weight:600;font-size:12.5px;color:#222;white-space:nowrap}
.perk span.c{width:42px;height:42px;border-radius:50%;background:var(--blue);display:flex;align-items:center;justify-content:center}

/* testimonials */
.clients{top:2132px;height:347px;background:#fff}
.clients .sec-title{top:38px;font-size:23px}
.quote{position:absolute;left:200px;top:115px;width:803px;font-size:12px;line-height:23px;font-style:italic;text-align:center;color:#444}
.person{position:absolute;left:643px;top:229px}
.person h5{font-family:"Montserrat",sans-serif;font-weight:600;font-size:18px;color:var(--blue)}
.person span{font-size:12px;color:#666;display:block;margin-top:6px}

/* support band */
.support{top:2479px;height:163px;background:linear-gradient(90deg,var(--green-a),var(--green-b))}
.support h2{position:absolute;left:0;width:1200px;top:36px;text-align:center;font-style:italic;font-weight:700;font-size:25px;color:#fff}
.help{position:absolute;top:94px;display:flex;gap:14px;color:#fff;white-space:nowrap}
.help strong{display:block;font-style:italic;font-weight:600;font-size:18px}
.help small{display:block;font-size:12px;color:#e8f3da;margin-top:2px}

/* footer */
.site-footer{top:2642px;height:69px;background:var(--footer);color:#fff;font-family:"Montserrat",sans-serif;font-weight:600;font-size:13px;white-space:nowrap}
.foot-links{position:absolute;left:99px;top:26px}
.foot-social{position:absolute;left:622px;top:27px;display:flex;gap:13px}
.foot-social span{width:14px;height:14px;border-radius:50%;background:#fff;display:block}
.copy{position:absolute;right:99px;top:27px;font-size:12px}
</style>
</head>
<body>

<header class="topbar">
  <div class="social"><span></span><span></span><span></span><span></span><span></span></div>
  <div class="contact-item" style="left:718px">
    <svg width="18" height="13" viewBox="0 0 18 13"><rect x="0.5" y="0.5" width="17" height="12" fill="#fff"/><path d="M1 1 L9 7 L17 1" stroke="#151515" stroke-width="1.5" fill="none"/></svg>
    info@ridgewaybanners.example
  </div>
  <div class="contact-item" style="left:978px">
    <svg width="15" height="15" viewBox="0 0 24 24"><path fill="#fff" d="M6.6 10.8a15.1 15.1 0 006.6 6.6l2.2-2.2a1 1 0 011-.25 11.4 11.4 0 003.6.57 1 1 0 011 1V20a1 1 0 01-1 1A17 17 0 013 4a1 1 0 011-1h3.5a1 1 0 011 1c0 1.25.2 2.45.57 3.57a1 1 0 01-.25 1z"/></svg>
    123-456-7890
  </div>
</header>

<header class="site-header">
  <div class="brand"><i></i>Ridgeway Banners</div>
  <nav class="nav">
    <a class="current">Home</a><span class="sep"></span>
    <a>About Us</a><span class="sep"></span>
    <a>Product</a><span class="sep"></span>
    <a>Category</a><span class="sep"></span>
    <a>FAQ's</a><span class="sep"></span>
    <a>Contact Us</a>
  </nav>
</header>

<section class="hero" role="img" aria-label="City harbour skyline at dusk with a collage of printed banners and signage">
  <h1 class="hero-title">We Are A New Australian Firm Which Will Sell Large Format Printed Banners And Other Signage Material</h1>
  <div class="btn-yellow">CONACT NOW !</div>
  <div class="tile" style="left:725px;top:42px;width:215px;height:121px;background:linear-gradient(135deg,#8fa8c4,#c9463c)" role="img" aria-label="Trade show hall with banners"></div>
  <div class="tile" style="left:600px;top:75px;width:195px;height:118px;background:linear-gradient(135deg,#b4383d,#d8c9c0)" role="img" aria-label="Printed banner being rolled"></div>
  <div class="tile" style="left:555px;top:153px;width:205px;height:124px;background:linear-gradient(135deg,#d6c68c,#3d7fbf)" role="img" aria-label="Flag banners on a beach"></div>
  <div class="tile" style="left:728px;top:228px;width:200px;height:118px;background:linear-gradient(135deg,#d6d0c6,#b63b36)" role="img" aria-label="Banner printing workshop"></div>
  <div class="tile" style="left:913px;top:266px;width:205px;height:122px;background:linear-gradient(135deg,#d9a521,#3a62a0)" role="img" aria-label="Stack of printed signage"></div>
  <div class="tile" style="left:1000px;top:146px;width:122px;height:136px;background:linear-gradient(135deg,#c9c2ba,#6f6f78)" role="img" aria-label="Staff at a large format printer"></div>
  <div class="dots"><span></span><span class="on"></span><span></span><span></span></div>
</section>

<section class="about">
  <h2 class="sec-title" style="top:32px;font-size:23px">ABOUT RIDGEWAY BANNERS</h2>
  <div class="rule" style="left:330px;top:80px;width:540px"></div>
  <p>Lorem ipsum dolor sit amet, consectetur adipiscing elit. Aenean et dignissim sem, interdum risus. Vestibulum consectetur nisi mollis diam pulvinar adipiscing. Vestibulum ut urna nec nibh adipiscing facilisis. Etiam auctor porta lacus ac luctus. Praesent ac libero fermentum, rhoncus magna a, dapibus mauris. Nam ut auctor justo. Sed ante odio, luctus quis nequ nec, adipiscing eleifend arcu. Integer nunc turpis, porttitor at lorem ut.Quisque hendrerit</p>
  <div class="btn-outline" style="left:540px;top:191px;width:120px;height:31px">READ MORE</div>
</section>

<section class="features">
  <div class="feature" style="left:93px">
    <div class="icon"><svg width="46" height="46" viewBox="0 0 24 24"><path fill="#fff" d="M2 10h4v11H2zM8 21V10l5-8c1.4 0 2.3 1 2 2.4L14 9h6a2 2 0 012 2.3l-1.4 7.8A2.3 2.3 0 0118.3 21z"/></svg></div>
    <h3>Quality Printing</h3>
    <p>Lorem ipsum dolor sit amet, consectetur adipiscing elit. Aenean et dignissim sem, interdum risus.</p>
    <div class="btn-outline">READ MORE</div>
  </div>
  <div class="feature" style="left:350px">
    <div class="icon"><svg width="46" height="46" viewBox="0 0 24 24" fill="none" stroke="#fff" stroke-width="2"><circle cx="13" cy="13" r="8"/><path d="M13 9v4l3 2M10 2h6M3 11h3M2 15h4M4 19h3"/></svg></div>
    <h3>Timely Delivery</h3>
    <p>Lorem ipsum dolor sit amet, consectetur adipiscing elit. Aenean et dignissim sem, interdum risus.</p>
    <div class="btn-outline">READ MORE</div>
  </div>
  <div class="feature" style="left:606px">
    <div class="icon"><svg width="46" height="46" viewBox="0 0 24 24" fill="none" stroke="#fff" stroke-width="2"><circle cx="12" cy="12" r="9"/><path d="M8 15c0-5 4-8 9-8-1 5-4 8-9 8zM8 15l-2 3"/></svg></div>
    <h3>Eco-Minded</h3>
    <p>Lorem ipsum dolor sit amet, consectetur adipiscing elit. Aenean et dignissim sem, interdum risus.</p>
    <div class="btn-outline">READ MORE</div>
  </div>
  <div class="feature" style="left:867px">
    <div class="icon"><svg width="46" height="46" viewBox="0 0 24 24"><path fill="#fff" d="M3 12h4v9H3zM9 20v-7l3-2h5a1.5 1.5 0 010 3h-3M9 20h8l5-5"/><rect x="11" y="3" width="9" height="6" rx="1" fill="#fff"/></svg></div>
    <h3>Money Back Guaranteed</h3>
    <p>Lorem ipsum dolor sit amet, consectetur adipiscing elit. Aenean et dignissim sem, interdum risus.</p>
    <div class="btn-outline">READ MORE</div>
  </div>
</section>

<section class="products" role="img" aria-label="Background of printed stickers and labels">
  <div class="shade"></div>
  <h2 class="sec-title">PRODUCT CATEGORIES</h2>

  <div class="photo" style="left:98px;top:135px;background:linear-gradient(135deg,#a9a9a5,#d9d7d2)" role="img" aria-label="Large format printer with stacked sheets"></div>
  <div class="card white" style="left:98px;top:316px"><h4>Lorem ipsum dolor sit</h4><p>Lorem ipsum dolor sit amet, consectetur adipiscing elit. Aenean et dignissim sem, interdum risus.</p><div class="btn-outline">READ MORE</div></div>

  <div class="card blue" style="left:352px;top:135px"><h4>Lorem ipsum dolor sit</h4><p>Lorem ipsum dolor sit amet, consectetur adipiscing elit. Aenean et dignissim sem, interdum risus.</p><div class="btn-outline">READ MORE</div></div>
  <div class="photo" style="left:352px;top:316px;background:linear-gradient(135deg,#3a3f46,#b24a7a 50%,#d8c36a)" role="img" aria-label="Colour print running through a printer"></div>

  <div class="photo" style="left:607px;top:135px;background:linear-gradient(135deg,#c9b6a0,#7aa1c9)" role="img" aria-label="Retail display with printed wall graphics"></div>
  <div class="card white" style="left:607px;top:316px"><h4>Lorem ipsum dolor sit</h4><p>Lorem ipsum dolor sit amet, consectetur adipiscing elit. Aenean et dignissim sem, interdum risus.</p><div class="btn-outline">READ MORE</div></div>

  <div class="card blue" style="left:862px;top:135px"><h4>Lorem ipsum dolor sit</h4><p>Lorem ipsum dolor sit amet, consectetur adipiscing elit. Aenean et dignissim sem, interdum risus.</p><div class="btn-outline">READ MORE</div></div>
  <div class="photo" style="left:862px;top:316px;background:linear-gradient(135deg,#3c7fb0,#7cba52 55%,#e0c64a)" role="img" aria-label="Printing rollers with colourful output"></div>
</section>

<section class="why">
  <h2>WHY CHOOSE <b>RIDGEWAY</b> BANNERS</h2>
  <p>Lorem ipsum dolor sit amet, consectetur adipiscing elit. Aenean et dignissim sem, interdum risus. Vestibulum consectetur nisi mollis diam pulvinar adipisc Vestibulum ut urna nec nibh adipiscing facilisis Lorem ipsum dolor sit amet, consectetur adipiscing elit.</p>
  <div class="perk" style="left:99px;top:205px"><span class="c"><svg width="22" height="22" viewBox="0 0 24 24" fill="none" stroke="#fff" stroke-width="2"><circle cx="12" cy="9" r="6"/><path d="M8 14l-2 8 6-3 6 3-2-8"/></svg></span>100% Quality Guarantee</div>
  <div class="perk" style="left:360px;top:205px"><span class="c"><svg width="22" height="22" viewBox="0 0 24 24" fill="none" stroke="#fff" stroke-width="2"><circle cx="12" cy="12" r="9"/><path d="M15 9h-4a1.5 1.5 0 000 3h2a1.5 1.5 0 010 3H9M12 7v10"/></svg></span>Best Price Guarantee</div>
  <div class="perk" style="left:99px;top:266px"><span class="c"><svg width="24" height="20" viewBox="0 0 24 20"><path fill="#fff" d="M1 3h13v11H1zM14 7h5l4 4v3h-9z"/><circle cx="6" cy="16" r="2.5" fill="#fff"/><circle cx="18" cy="16" r="2.5" fill="#fff"/></svg></span>Free Shipping</div>
  <div class="perk" style="left:360px;top:266px"><span class="c"><svg width="22" height="22" viewBox="0 0 24 24" fill="none" stroke="#fff" stroke-width="2"><rect x="3" y="5" width="18" height="12"/><path d="M9 21h6M12 17v4M8 14l7-7"/></svg></span>Free Design Proofs</div>
  <div class="abs" style="left:600px;top:3px;width:600px;height:354px;background:linear-gradient(135deg,#c9ccd0,#eceded 50%,#9ea3a8)" role="img" aria-label="Staff member operating an office printer"></div>
</section>

<section class="clients">
  <h2 class="sec-title">WHAT OUR CLIENTS SAY</h2>
  <div class="rule" style="left:330px;top:82px;width:540px"></div>
  <svg class="abs" style="left:100px;top:136px" width="28" height="58" viewBox="0 0 28 58"><path d="M26 2 L3 29 L26 56" fill="none" stroke="#888" stroke-width="2"/></svg>
  <svg class="abs" style="left:1072px;top:136px" width="28" height="58" viewBox="0 0 28 58"><path d="M2 2 L25 29 L2 56" fill="none" stroke="#888" stroke-width="2"/></svg>
  <p class="quote">Lorem ipsum dolor sit amet, consectetuer adipiscing elit, sed diam nonummy nibh euismod tincidunt ut laoreet dolore magna aliquam erat volutpat. Ut wisi enim minim veniam, quis nostrud exerci tation ullamcorper suscipit lobortis nisl ut aliquip ex ea commodo consequat. Ut wisi enim minim veniam, quis nostrud exerci tation ullamcorper suscipit lobortis nisl ut aliquip ex ea commodo consequat.</p>
  <div class="abs" style="left:478px;top:230px;width:66px;height:66px;border-radius:50%;background:var(--blue);display:flex;align-items:center;justify-content:center"><svg width="30" height="26" viewBox="0 0 30 26"><path fill="#fff" d="M2 14C2 6 6 2 12 1v4c-3 1-5 3-5 7h5v12H2zM17 14c0-8 4-12 10-13v4c-3 1-5 3-5 7h5v12H17z"/></svg></div>
  <div class="abs" style="left:540px;top:217px;width:82px;height:82px;border-radius:50%;border:3px solid var(--blue);background:linear-gradient(135deg,#d8c3ae,#8c9aa8)" role="img" aria-label="Portrait of the client"></div>
  <div class="person"><h5>Liam Carver</h5><span>Lorem Ipsum</span></div>
</section>

<section class="support">
  <h2>We're Dedicated to Our Customers 24x7</h2>
  <div class="help" style="left:99px"><svg width="38" height="38" viewBox="0 0 24 24"><path fill="#fff" d="M6.6 10.8a15.1 15.1 0 006.6 6.6l2.2-2.2a1 1 0 011-.25 11.4 11.4 0 003.6.57 1 1 0 011 1V20a1 1 0 01-1 1A17 17 0 013 4a1 1 0 011-1h3.5a1 1 0 011 1c0 1.25.2 2.45.57 3.57a1 1 0 01-.25 1z"/></svg><div><strong>123-456-7890</strong><small>Available 24/7 - Call us any time.</small></div></div>
  <div class="help" style="left:419px"><svg width="44" height="36" viewBox="0 0 44 36" fill="none" stroke="#fff" stroke-width="2.5"><rect x="2" y="4" width="40" height="28"/><path d="M2 4l20 16 20-16M2 32l15-13M42 32L27 19"/></svg><div><strong>Email Us</strong><small>Have a question? Let us help.</small></div></div>
  <div class="help" style="left:726px"><svg width="44" height="36" viewBox="0 0 44 36" fill="none" stroke="#fff" stroke-width="2.5"><ellipse cx="18" cy="14" rx="15" ry="10"/><path d="M10 22l-4 8 10-6M30 21c6 0 11-3 11-8"/></svg><div><strong>Live Chat</strong><small>Online Support</small></div></div>
  <div class="help" style="left:934px"><svg width="26" height="38" viewBox="0 0 26 38"><path d="M4 11a9 9 0 1118 0c0 6-9 7-9 14" fill="none" stroke="#fff" stroke-width="4"/><circle cx="13" cy="33" r="3" fill="#fff"/></svg><div><strong>Help</strong><small>Find your answers.</small></div></div>
</section>

<footer class="site-footer">
  <div class="foot-links">Home &nbsp;/&nbsp; About Us &nbsp;/&nbsp; Product &nbsp;/&nbsp; Category &nbsp;/&nbsp; FAQ's &nbsp;/&nbsp; Contact Us</div>
  <div class="foot-social"><span></span><span></span><span></span><span></span><span></span></div>
  <div class="copy">© 2016 RIDGEWAY BANNERS. ALL RIGHTS RESERVED.</div>
</footer>

</body>
</html>
```